Full Page Tolver 250 Ad

We need a full page magazine ad. Our company is a site construction company - meaning we build lakes, ponds, do brush clearing for farmers and ranchers. For commercial customers, we build building pads, site clearing, pavement and soil stabilization. The final design should show what we do. Our website is www.pendrowgrading.com

```html
<!DOCTYPE html>
<html lang="en">
<head>
<meta charset="utf-8">
<title>Tolver 250 – Full Page Ad</title>
<link href="https://fonts.googleapis.com/css2?family=Alfa+Slab+One&family=Montserrat:wght@500;600;700;800&family=Oswald:wght@600&display=swap" rel="stylesheet">
<style>
  :root{
    --yellow:#f8b845;
    --blue:#2a62b0;
    --dark:#262626;
    --black:#0a0a0a;
    --red:#d90b0b;
    --white:#ffffff;
    --ink:#111111;
  }
  *{margin:0;padding:0;box-sizing:border-box}
  html,body{width:921px;height:1200px;overflow:hidden;background:var(--white)}
  .ad{position:relative;width:921px;height:1200px;background:var(--white);font-family:"Montserrat",sans-serif;overflow:hidden}
  .top-bar{position:absolute;left:453px;top:0;width:468px;height:36px;background:var(--black)}
  .services-panel{position:absolute;left:0;top:528px;width:453px;height:480px;background:var(--yellow)}
  .services-dark{position:absolute;left:453px;top:528px;width:468px;height:480px;background:linear-gradient(160deg,#3a3a3a,#1f1f1f 60%,#2c2c2c)}
  .hero-frame{position:absolute;left:36px;top:45px;width:885px;height:523px;background:var(--yellow);border-radius:62px 0 0 62px}
  .hero-frame::after{content:"";position:absolute;left:-8px;bottom:-9px;width:893px;height:9px;background:var(--white);border-radius:0 0 0 40px;z-index:-1}
  .hero-photo{position:absolute;left:55px;top:64px;width:866px;height:484px;border-radius:46px 0 0 46px;
    background:linear-gradient(180deg,#2a5fae 0%,#4a86c4 32%,#b8cde0 48%,#8c8a6a 60%,#5e5446 72%,#8e7f6a 86%,#a8977d 100%)}
  .hazard{position:absolute}
  .headline{position:absolute;left:115px;top:96px;font-family:"Alfa Slab One",serif;font-size:41px;line-height:46px;letter-spacing:.3px;text-transform:uppercase}
  .headline .gold{color:var(--yellow)}
  .headline .light{color:var(--white)}
  .badge{position:absolute;left:560px;top:425px;width:228px;height:228px}
  .services-title{position:absolute;left:105px;top:597px;font-weight:800;font-size:36px;color:var(--ink);letter-spacing:.2px}
  .tile{position:absolute;width:204px;height:153px;border:4px solid var(--white);border-radius:10px}
  .tile-lake{left:101px;top:673px;background:linear-gradient(180deg,#c8d6e4 0%,#8aa6b8 45%,#7fa04a 70%,#4c6a2c 100%)}
  .tile-aerial{left:317px;top:673px;background:linear-gradient(135deg,#5d5a52,#7b786d 55%,#cfcbbf 80%,#6d7a66)}
  .tile-shore{left:101px;top:841px;background:linear-gradient(180deg,#9fc3e6 0%,#d4e4f2 25%,#5f8e8f 42%,#6d6456 65%,#3e362d 100%)}
  .tile-scraper{left:317px;top:841px;background:linear-gradient(160deg,#c9cfd4 0%,#b9913e 40%,#8a6d3a 65%,#9d9a92 100%)}
  .service-group{position:absolute;left:575px}
  .service-group h3{font-weight:800;font-size:18.5px;line-height:21px;color:var(--yellow);text-transform:uppercase}
  .service-group ul{list-style:none;margin-top:7px}
  .service-group li{display:flex;align-items:center;gap:12px;height:27.5px;color:var(--white);font-size:16px;font-weight:600}
  .service-group li svg{flex:none}
  .farm{top:677px}
  .commercial{top:848px}
  .bottom-bar{position:absolute;left:0;top:1006px;width:921px;height:15px;background:var(--black)}
  .brand{position:absolute;left:70px;top:1080px;display:flex;align-items:center;gap:10px}
  .brand-mark{width:22px;height:22px;background:var(--yellow)}
  .brand-name{font-weight:800;font-size:32px;color:var(--ink)}
  .contact{position:absolute;top:1057px}
  .contact-a{left:350px}
  .contact-b{left:615px}
  .contact .name{display:inline-block;background:var(--black);color:var(--white);font-weight:600;font-size:17px;line-height:21px;padding:0 8px;width:182px}
  .contact .line{display:flex;align-items:center;gap:5px;font-size:11.5px;font-weight:500;color:var(--ink);margin-top:4px}
  .contact .line:first-of-type{margin-top:6px}
  .website{position:absolute;left:348px;top:1124px;font-weight:600;font-size:36px;letter-spacing:.5px;color:var(--ink)}
</style>
</head>
<body>
<main class="ad">
  <div class="top-bar"></div>
  <div class="services-panel"></div>
  <div class="services-dark"></div>

  <div class="hero-frame"></div>
  <div class="hero-photo" role="img" aria-label="Tractor pulling a scraper across freshly graded ranch land under a blue sky with scattered oak trees"></div>

  <svg class="hazard" style="left:168px;top:45px" width="80" height="19" viewBox="0 0 80 19">
    <polygon points="8,19 18,0 28,0 18,19" fill="#0a0a0a"/>
    <polygon points="28,19 38,0 48,0 38,19" fill="#0a0a0a"/>
    <polygon points="48,19 58,0 68,0 58,19" fill="#0a0a0a"/>
  </svg>

  <h1 class="headline">
    <span class="gold">Commercial Site<br>Construction, Farm &amp;</span><br>
    <span class="light">Ranch Projects to<br>Oilfield Services</span>
  </h1>

  <svg class="badge" viewBox="0 0 228 228" aria-label="With over 50 years experience">
    <polygon fill="#c20a0a" points="114,0 126,17 141,3 148,23 166,12 168,34 188,28 185,50 206,49 197,69 218,73 204,90 223,101 205,114 223,127 204,138 218,155 197,159 206,179 185,178 188,200 168,194 166,216 148,205 141,225 126,211 114,228 102,211 87,225 80,205 62,216 60,194 40,200 43,178 22,179 31,159 10,155 24,138 5,127 23,114 5,101 24,90 10,73 31,69 22,49 43,50 40,28 60,34 62,12 80,23 87,3 102,17"/>
    <circle cx="114" cy="114" r="88" fill="#e50d0d"/>
    <circle cx="114" cy="114" r="84" fill="none" stroke="#ffffff" stroke-width="1.2"/>
    <defs>
      <path id="arcTop" d="M50,114 A64,64 0 0 1 178,114"/>
      <path id="arcBottom" d="M44,120 A70,70 0 0 0 184,120"/>
    </defs>
    <text font-family="Oswald, sans-serif" font-weight="600" font-size="21" fill="#ffffff" letter-spacing="1"><textPath href="#arcTop" startOffset="50%" text-anchor="middle">WITH OVER</textPath></text>
    <text font-family="Oswald, sans-serif" font-weight="600" font-size="21" fill="#f8b845" letter-spacing="1.5"><textPath href="#arcBottom" startOffset="50%" text-anchor="middle">EXPERIENCE</textPath></text>
    <text x="114" y="130" text-anchor="middle" font-family="Montserrat, sans-serif" font-weight="800" font-size="58" fill="#ffffff">50</text>
    <text x="114" y="160" text-anchor="middle" font-family="Montserrat, sans-serif" font-weight="800" font-size="23" fill="#ffffff">YEARS</text>
    <g fill="#ffffff" font-size="11" font-family="Montserrat, sans-serif">
      <text x="42" y="103">★</text><text x="36" y="117">★</text><text x="42" y="131">★</text>
      <text x="176" y="103">★</text><text x="182" y="117">★</text><text x="176" y="131">★</text>
    </g>
  </svg>

  <h2 class="services-title">OUR SERVICES</h2>
  <div class="tile tile-lake" role="img" aria-label="Finished ranch lake with grassy bank and wild birds along the shore"></div>
  <div class="tile tile-aerial" role="img" aria-label="Aerial view of a cleared and graded commercial building pad"></div>
  <div class="tile tile-shore" role="img" aria-label="Tractor and scraper shaping a shoreline beside open water"></div>
  <div class="tile tile-scraper" role="img" aria-label="Yellow earthmoving scraper hitched to a red tractor on graded soil"></div>

  <section class="service-group farm">
    <h3>For farmers and<br>ranchers</h3>
    <ul>
      <li><svg width="15" height="17" viewBox="0 0 15 17"><polygon points="7.5,0 15,4.25 15,12.75 7.5,17 0,12.75 0,4.25" fill="#f8b845"/></svg>Build lakes</li>
      <li><svg width="15" height="17" viewBox="0 0 15 17"><polygon points="7.5,0 15,4.25 15,12.75 7.5,17 0,12.75 0,4.25" fill="#f8b845"/></svg>Ponds</li>
      <li><svg width="15" height="17" viewBox="0 0 15 17"><polygon points="7.5,0 15,4.25 15,12.75 7.5,17 0,12.75 0,4.25" fill="#f8b845"/></svg>Do brush clearing</li>
    </ul>
  </section>

  <section class="service-group commercial">
    <h3>For commercial<br>customers</h3>
    <ul>
      <li><svg width="15" height="17" viewBox="0 0 15 17"><polygon points="7.5,0 15,4.25 15,12.75 7.5,17 0,12.75 0,4.25" fill="#f8b845"/></svg>Build building pads</li>
      <li><svg width="15" height="17" viewBox="0 0 15 17"><polygon points="7.5,0 15,4.25 15,12.75 7.5,17 0,12.75 0,4.25" fill="#f8b845"/></svg>Site clearing</li>
      <li><svg width="15" height="17" viewBox="0 0 15 17"><polygon points="7.5,0 15,4.25 15,12.75 7.5,17 0,12.75 0,4.25" fill="#f8b845"/></svg>Pavement &amp; soil stabilization</li>
    </ul>
  </section>

  <div class="bottom-bar"></div>
  <svg class="hazard" style="left:0;top:1006px" width="104" height="15" viewBox="0 0 104 15">
    <rect width="104" height="15" fill="#ffffff"/>
    <polygon points="0,15 8,0 16,0 8,15" fill="#0a0a0a"/>
    <polygon points="16,15 24,0 32,0 24,15" fill="#f8b845"/>
    <polygon points="32,15 40,0 48,0 40,15" fill="#0a0a0a"/>
    <polygon points="48,15 56,0 64,0 56,15" fill="#f8b845"/>
    <polygon points="64,15 72,0 80,0 72,15" fill="#0a0a0a"/>
    <polygon points="80,15 88,0 96,0 88,15" fill="#f8b845"/>
  </svg>

  <div class="brand">
    <span class="brand-mark"></span>
    <span class="brand-name">Tolver 250</span>
  </div>

  <div class="contact contact-a">
    <span class="name">Dana Whitfield</span>
    <div class="line"><svg width="10" height="10" viewBox="0 0 24 24"><path fill="#111" d="M6.6 10.8a15.1 15.1 0 0 0 6.6 6.6l2.2-2.2a1 1 0 0 1 1-.25 11.4 11.4 0 0 0 3.6.57 1 1 0 0 1 1 1V20a1 1 0 0 1-1 1A17 17 0 0 1 3 4a1 1 0 0 1 1-1h3.5a1 1 0 0 1 1 1c0 1.25.2 2.45.57 3.57a1 1 0 0 1-.25 1z"/></svg>555.210.4471</div>
    <div class="line"><svg width="10" height="10" viewBox="0 0 24 24"><path fill="#111" d="M2 5h20v14H2z M2 5l10 7 10-7" stroke="#fff" stroke-width="1.5"/></svg>dana@pendrowgrading.com</div>
  </div>

  <div class="contact contact-b">
    <span class="name">Cole Whitfield</span>
    <div class="line"><svg width="10" height="10" viewBox="0 0 24 24"><path fill="#111" d="M6.6 10.8a15.1 15.1 0 0 0 6.6 6.6l2.2-2.2a1 1 0 0 1 1-.25 11.4 11.4 0 0 0 3.6.57 1 1 0 0 1 1 1V20a1 1 0 0 1-1 1A17 17 0 0 1 3 4a1 1 0 0 1 1-1h3.5a1 1 0 0 1 1 1c0 1.25.2 2.45.57 3.57a1 1 0 0 1-.25 1z"/></svg>555.210.4486</div>
    <div class="line"><svg width="10" height="10" viewBox="0 0 24 24"><path fill="#111" d="M2 5h20v14H2z M2 5l10 7 10-7" stroke="#fff" stroke-width="1.5"/></svg>cole@pendrowgrading.com</div>
  </div>

  <p class="website">www.pendrowgrading.com</p>
</main>
</body>
</html>
```